Maple Roster Business Card for recruitment company

We are looking for a Business Card Design that incorporates our personal details and our busines name and logo. We are a specialized search consultancy that recruit Property and Construction professionals.
We would like a business card that stands out and is appealing to the Construction and Property industry as well.

Target Market(s)

people in the construction and property industry

Contact Information for Business Card

Business Name and logo

Font styles to use
Serif

Colors
0094D4
00A9DD
6FCCEA
C7EBF8
E9F6FB

Requirements
Must have
• Business name and logo as well as contact details
Should not have
• No photos of us please

```html
<!DOCTYPE html>
<html lang="en">
<head>
<meta charset="UTF-8">
<title>Maple Roster Business Card</title>
<link href="https://fonts.googleapis.com/css2?family=Libre+Baskerville:wght@400;700&display=swap" rel="stylesheet">
<style>
  :root {
    --backdrop: #2a2a2a;
    --blue: #0094d4;
    --blue-bright: #00a9dd;
    --blue-soft: #6fccea;
    --blue-pale: #c7ebf8;
    --blue-mist: #e9f6fb;
    --paper: #ffffff;
  }
  * { margin: 0; padding: 0; box-sizing: border-box; }
  html, body { width: 1200px; height: 1015px; overflow: hidden; }
  body {
    background: var(--backdrop);
    font-family: "Libre Baskerville", Georgia, serif;
    display: flex;
    flex-direction: column;
    align-items: center;
    justify-content: center;
    gap: 60px;
  }
  .card {
    width: 640px;
    height: 366px;
    position: relative;
    overflow: hidden;
  }
  .brand {
    display: flex;
    align-items: center;
    justify-content: center;
    gap: 16px;
  }
  .brand-mark {
    width: 26px;
    height: 26px;
    border-radius: 50%;
    flex: none;
  }
  .brand-name {
    font-weight: 400;
    font-size: 44px;
    letter-spacing: 4px;
    text-transform: uppercase;
    white-space: nowrap;
    line-height: 1;
  }
  .card-back {
    background: var(--blue);
    display: flex;
    align-items: center;
    justify-content: center;
  }
  .card-back .brand-name { color: var(--blue-pale); }
  .card-back .brand-mark { background: var(--blue-soft); }

  .card-front { background: var(--paper); }
  .card-front .brand {
    position: absolute;
    top: 102px;
    left: 0;
    right: 0;
  }
  .card-front .brand-name { color: var(--blue); }
  .card-front .brand-mark { background: var(--blue-bright); }
  .rule {
    position: absolute;
    left: 0;
    right: 0;
    height: 2px;
    background: var(--blue);
  }
  .rule-top { top: 188px; }
  .rule-bottom { top: 300px; }
  .info-band {
    position: absolute;
    top: 196px;
    left: 0;
    right: 0;
    height: 98px;
    background: var(--blue);
    color: var(--paper);
    display: flex;
    align-items: center;
  }
  .person {
    width: 330px;
    text-align: center;
    text-transform: uppercase;
  }
  .person-name { font-size: 19px; font-weight: 700; letter-spacing: 0.5px; }
  .person-role { font-size: 12px; letter-spacing: 0.5px; margin-top: 4px; color: var(--blue-mist); }
  .band-divider {
    width: 1px;
    height: 98px;
    background: var(--paper);
  }
  .contact-list {
    list-style: none;
    padding-left: 24px;
    font-size: 13px;
    line-height: 24px;
  }
  .contact-list li { display: flex; align-items: center; gap: 8px; white-space: nowrap; }
  .contact-list svg { width: 14px; height: 14px; flex: none; }
  .address {
    position: absolute;
    top: 320px;
    left: 0;
    right: 0;
    text-align: center;
    color: var(--blue);
    font-size: 13px;
  }
</style>
</head>
<body>
  <section class="card card-back">
    <div class="brand">
      <span class="brand-mark"></span>
      <span class="brand-name">Maple Roster</span>
    </div>
  </section>

  <section class="card card-front">
    <div class="brand">
      <span class="brand-mark"></span>
      <span class="brand-name">Maple Roster</span>
    </div>
    <div class="rule rule-top"></div>
    <div class="info-band">
      <div class="person">
        <div class="person-name">Daniel Reyes</div>
        <div class="person-role">Managing Director</div>
      </div>
      <div class="band-divider"></div>
      <ul class="contact-list">
        <li>
          <svg viewBox="0 0 16 16" aria-hidden="true"><path d="M3 1.5h3l1.2 3.2-1.8 1.2a8 8 0 0 0 4.7 4.7l1.2-1.8 3.2 1.2v3a1.5 1.5 0 0 1-1.6 1.5C6.7 14 2 9.3 1.5 3.1A1.5 1.5 0 0 1 3 1.5z" fill="none" stroke="#fff" stroke-width="1.5"/></svg>
          055-210 384 617
        </li>
        <li>
          <svg viewBox="0 0 16 16" aria-hidden="true"><rect x="1" y="3" width="14" height="10" fill="none" stroke="#fff" stroke-width="1.5"/><path d="M1 3l7 6 7-6" fill="none" stroke="#fff" stroke-width="1.5"/></svg>
          hello@mapleroster.com
        </li>
        <li>
          <svg viewBox="0 0 16 16" aria-hidden="true"><circle cx="8" cy="8" r="6.5" fill="none" stroke="#fff" stroke-width="1.3"/><ellipse cx="8" cy="8" rx="3" ry="6.5" fill="none" stroke="#fff" stroke-width="1.2"/><path d="M1.5 8h13M2.5 4.7h11M2.5 11.3h11" stroke="#fff" stroke-width="1.1"/></svg>
          www.mapleroster.com
        </li>
      </ul>
    </div>
    <div class="rule rule-bottom"></div>
    <p class="address">421, Address line goes here, 45452, Country Name</p>
  </section>
</body>
</html>
```